NEW Modern Sleek Business Card for VR Language Startup

Our startup is using VR to lead the next wave of world language education. We need a two-sided business card that introduces the larger organization (Brightloom Language Inc) and our contact info on one side and shows the product, Glimwoorld, on the other side.

Side 1 (contact info)= Brightloom Logo and Contact info (name, title, phone, email)

Side 2 (product)= Glimworld logo, text, and website
Text= Culturally Immersive Language Learning Games
Website= www.glimworld-play.com

Target Market(s)

Education, Technology

Contact Information for Business Card

Contact info will be updated upon approval of the design. For now, put this as a placeholder.

Perry Dunmore
Founder & CEO
pdunmore@quillpost-mail.net
(555)-014-2286

Font styles to use
Other font styles liked:
• Gibson and Century Gothic are the brand fonts

Requirements
Nice to have
• I would love to see cohesion between the design and colors of the two logos. I have attached a few business card designs that I like, so you can get a feel for my preferred style.

```html
<!DOCTYPE html>
<html lang="en">
<head>
<meta charset="utf-8">
<title>Brightloom Language — Business Card</title>
<link rel="stylesheet" href="https://fonts.googleapis.com/css2?family=Questrial&display=swap">
<style>
  :root {
    --page: #ffffff;
    --blue-deep: #0892cf;
    --blue-bright: #05adeb;
    --white: #ffffff;
    --ink-grey: #6d6e71;
    --edge: #e6e7e8;
    --shade: rgba(0, 0, 0, 0.16);
  }
  * { box-sizing: border-box; margin: 0; padding: 0; }
  html, body {
    width: 1200px; height: 1000px; overflow: hidden;
    background: var(--page);
    font-family: "Questrial", "Century Gothic", sans-serif;
  }
  .canvas { position: relative; width: 1200px; height: 1000px; }

  .card {
    position: absolute; left: 365px; width: 513px; height: 294px;
  }
  .card::after {
    content: ""; position: absolute; left: 6%; right: 6%; bottom: -9px; height: 10px;
    background: radial-gradient(ellipse at top, var(--shade), transparent 70%);
    z-index: -1;
  }
  .surface-blue {
    background: linear-gradient(135deg, var(--blue-deep) 0%, var(--blue-bright) 55%, var(--blue-deep) 100%);
  }

  /* Product side */
  .card--product { top: 150px; color: var(--white); }
  .product-mark { position: absolute; left: 42px; top: 34px; display: flex; flex-direction: column; gap: 10px; }
  .product-mark .dot { width: 46px; height: 46px; border-radius: 50%; background: var(--white); margin-left: 22px; }
  .product-mark .name { font-size: 23px; line-height: 1; color: var(--white); }
  .tagline {
    position: absolute; left: 42px; top: 158px;
    font-size: 22px; line-height: 28px; letter-spacing: 0.3px; text-transform: uppercase;
  }
  .website { position: absolute; left: 42px; top: 250px; font-size: 15.5px; letter-spacing: 0.4px; }

  /* Contact side */
  .card--contact { top: 527px; background: var(--white); border: 1px solid var(--edge); }
  .contact-split { position: absolute; inset: 0; width: 100%; height: 100%; }
  .org-mark { position: absolute; left: 40px; top: 30px; display: flex; flex-direction: column; gap: 14px; }
  .org-mark .dot { width: 46px; height: 46px; border-radius: 50%; background: var(--ink-grey); margin-left: 44px; }
  .org-mark .name { font-size: 23px; line-height: 1; letter-spacing: 1.5px; color: var(--ink-grey); }
  .contact-details { position: absolute; right: 34px; top: 96px; text-align: right; color: var(--white); }
  .person { font-size: 30px; line-height: 38px; white-space: nowrap; }
  .role { font-size: 18px; line-height: 24px; margin-top: 2px; letter-spacing: 0.3px; }
  .lines { margin-top: 42px; font-size: 14px; line-height: 22px; }
</style>
</head>
<body>
<main class="canvas">

  <section class="card card--product surface-blue" aria-label="Product side">
    <div class="product-mark">
      <span class="dot"></span>
      <span class="name">Glimworld</span>
    </div>
    <p class="tagline">Culturally immersive<br>language learning<br>games</p>
    <p class="website">www.glimworld-play.com</p>
  </section>

  <section class="card card--contact" aria-label="Contact side">
    <svg class="contact-split" viewBox="0 0 513 294" preserveAspectRatio="none" aria-hidden="true">
      <defs>
        <linearGradient id="blueField" x1="0" y1="0" x2="1" y2="1">
          <stop offset="0" stop-color="#0892cf"/>
          <stop offset="0.6" stop-color="#05adeb"/>
          <stop offset="1" stop-color="#0892cf"/>
        </linearGradient>
      </defs>
      <polygon points="339,0 346,0 53,294 46,294" fill="#0892cf"/>
      <polygon points="353,0 513,0 513,294 60,294" fill="url(#blueField)"/>
    </svg>
    <div class="org-mark">
      <span class="dot"></span>
      <span class="name">Brightloom</span>
    </div>
    <div class="contact-details">
      <p class="person">Perry Dunmore</p>
      <p class="role">FOUNDER &amp; CEO</p>
      <p class="lines">pdunmore@quillpost-mail.net<br>(555)-014-2286</p>
    </div>
  </section>

</main>
</body>
</html>
```